BUSINESS CARD DESIGN

NAME- DALE VORSKIN
PHONE NUMER - 555- 714-9082
EMAIL- OFFICE@TRV-GROUNDMAKRZ.COM
BACK OF CARD- SPEACIALIZES IN LAND CLEARING, FORESTRY MUCLHING AND EXCAVATION

Contact Information for Business Card

NAME- DALE VORSKIN PHONE NUMER - 555- 714-9082 EMAIL- OFFICE@TRV-GROUNDMAKRZ.COM BACK OF CARD- SPEACIALIZES IN LAND CLEARING , MUCLHING AND EXCAVATION

```html
<!DOCTYPE html>
<html lang="en">
<head>
<meta charset="utf-8">
<title>Trevane Groundmakrz – Business Card</title>
<link rel="stylesheet" href="https://fonts.googleapis.com/css2?family=Roboto:wght@400&family=Roboto+Condensed:wght@300;700&display=swap">
<style>
  :root {
    --page: #e2e6e7;
    --gold: #f5b31b;
    --gold-emboss: #fbd033;
    --charcoal: #222326;
    --charcoal-soft: #2c2d31;
    --white: #ffffff;
    --ink-soft: #ececec;
  }
  * { margin: 0; padding: 0; box-sizing: border-box; }
  html, body { width: 1200px; height: 960px; overflow: hidden; }
  body { background: var(--page); position: relative; font-family: "Roboto", sans-serif; }

  .card { position: absolute; overflow: hidden; box-shadow: 0 8px 18px rgba(0,0,0,.25); }

  /* Brand block (shared) */
  .brand {
    position: absolute; display: flex; flex-direction: column; align-items: center;
    font-family: "Roboto Condensed", sans-serif; font-weight: 700;
  }
  .brand-dot { border-radius: 50%; }
  .brand-name { white-space: nowrap; line-height: 1; }
  .brand-sub { display: flex; align-items: center; width: 100%; white-space: nowrap; line-height: 1; }
  .brand-sub::before, .brand-sub::after { content: ""; flex: 1; height: 2px; }
  .brand-rule { width: 100%; height: 2px; }
  .brand-phone { white-space: nowrap; line-height: 1; }

  /* Front */
  .card-front { left: 246px; top: 58px; width: 709px; height: 406px; background: var(--gold); }
  .front-brand { left: 206px; width: 297px; top: 81px; color: var(--gold-emboss); }
  .front-brand .brand-dot { width: 154px; height: 154px; background: var(--gold-emboss); margin-bottom: 16px; }
  .front-brand .brand-name { font-size: 23px; letter-spacing: 2.4px; }
  .front-brand .brand-sub { font-size: 14px; letter-spacing: 7px; margin-top: 8px; gap: 12px; }
  .front-brand .brand-sub::before, .front-brand .brand-sub::after,
  .front-brand .brand-rule { background: var(--gold-emboss); }
  .front-brand .brand-rule { margin-top: 9px; }
  .front-brand .brand-phone { font-size: 13px; letter-spacing: 15.5px; margin-top: 8px; margin-right: -15px; }

  .tagline {
    position: absolute; left: 0; right: 0; top: 361px; text-align: center;
    color: var(--white); font-size: 16.5px; letter-spacing: 0.5px; line-height: 1.2;
  }

  /* Back */
  .card-back { left: 250px; top: 500px; width: 701px; height: 400px; background: var(--charcoal); }
  .watermark {
    position: absolute; left: 20px; top: 30px; width: 345px; height: 345px; border-radius: 50%;
    background: radial-gradient(circle at 45% 40%, var(--charcoal-soft), #1a1b1e 75%);
  }
  .back-brand { left: 482px; width: 189px; top: 26px; color: var(--gold); }
  .back-brand .brand-dot { width: 97px; height: 97px; background: var(--gold); margin-bottom: 12px; }
  .back-brand .brand-name { font-size: 16px; letter-spacing: 1.2px; }
  .back-brand .brand-sub { font-size: 10px; letter-spacing: 5px; margin-top: 5px; gap: 8px; }
  .back-brand .brand-sub::before, .back-brand .brand-sub::after,
  .back-brand .brand-rule { background: var(--gold); height: 1.5px; }
  .back-brand .brand-rule { margin-top: 5px; }
  .back-brand .brand-phone { font-size: 9px; letter-spacing: 10px; margin-top: 5px; margin-right: -10px; }

  .holder {
    position: absolute; right: 30px; top: 228px;
    font-family: "Roboto Condensed", sans-serif; font-size: 45px; font-weight: 400;
    letter-spacing: 1.5px; color: var(--gold); line-height: 1; white-space: nowrap;
  }
  .holder .first { font-weight: 700; }
  .holder .last { font-weight: 300; }
  .holder-bar { position: absolute; right: 0; top: 232px; width: 19px; height: 30px; background: var(--gold); }

  .contact-list {
    position: absolute; right: 27px; top: 314px; list-style: none;
    display: flex; flex-direction: column; align-items: flex-end; gap: 4px;
  }
  .contact-list li {
    display: flex; align-items: center; gap: 9px;
    color: var(--ink-soft); font-size: 15px; letter-spacing: 0.6px; line-height: 17px; white-space: nowrap;
  }
  .contact-list svg { width: 15px; height: 15px; fill: var(--gold); }
</style>
</head>
<body>

  <section class="card card-front">
    <div class="brand front-brand">
      <span class="brand-dot"></span>
      <span class="brand-name">TREVANE GROUNDMAKRZ</span>
      <span class="brand-sub">LLC</span>
      <span class="brand-rule"></span>
      <span class="brand-phone">555-714-9082</span>
    </div>
    <p class="tagline">SPEACIALIZES IN LAND CLEARING , MUCLHING AND EXCAVATION</p>
  </section>

  <section class="card card-back">
    <div class="watermark" role="img" aria-label="Faint embossed brand watermark"></div>

    <div class="brand back-brand">
      <span class="brand-dot"></span>
      <span class="brand-name">TREVANE GROUNDMAKRZ</span>
      <span class="brand-sub">LLC</span>
      <span class="brand-rule"></span>
      <span class="brand-phone">555-714-9082</span>
    </div>

    <h1 class="holder"><span class="first">DALE</span> <span class="last">VORSKIN</span></h1>
    <span class="holder-bar"></span>

    <ul class="contact-list">
      <li>555- 714-9082
        <svg viewBox="0 0 24 24"><path d="M6.6 10.8a15.1 15.1 0 0 0 6.6 6.6l2.2-2.2a1 1 0 0 1 1-.25 11.4 11.4 0 0 0 3.6.57 1 1 0 0 1 1 1V20a1 1 0 0 1-1 1A17 17 0 0 1 3 4a1 1 0 0 1 1-1h3.5a1 1 0 0 1 1 1c0 1.25.2 2.45.57 3.6a1 1 0 0 1-.25 1z"/></svg>
      </li>
      <li>WWW.TRV-GROUNDMAKRZ.COM
        <svg viewBox="0 0 24 24"><path d="M12 2a10 10 0 1 0 0 20 10 10 0 0 0 0-20zm-1 17.9A8 8 0 0 1 4.2 10.2L9 15v1a2 2 0 0 0 2 2zm6.9-2.5A2 2 0 0 0 16 16h-1v-3a1 1 0 0 0-1-1H8v-2h2a1 1 0 0 0 1-1V7h2a2 2 0 0 0 2-2v-.4a8 8 0 0 1 2.9 12.8z"/></svg>
      </li>
      <li>OFFICE@TRV-GROUNDMAKRZ.COM
        <svg viewBox="0 0 24 24"><path d="M3 6h18v13H3zm2 2v.4l7 4.6 7-4.6V8l-7 4.5z"/></svg>
      </li>
    </ul>
  </section>

</body>
</html>
```